Visitenkarte für Ergotherapiepraxis
Zielgruppe
Wir arbeiten mit Kindern und Erwachsene jeden Alters.
Diese Personen kommen mit Beeinträchtigungen (körperlich, seelisch, schulisch) im täglichen Leben zu uns. Wir unterstützen unsere Patienten die Beeinträchtigungen zu verringern oder zu kompensieren und so den Alltag besser bewältigen zu können.
Aufgabenstellung
Ein Design was Kinder und Erwachsene anspricht, aber nicht zu verspielt wirkt. Es soll vertrauenserweckend sein. Eventuell sollte die Visitenkarte ein "aufgehendes oder erblühendes oder aufsteigendes" Element enthalten (=zu Beginn war die Beeinträchtigung dann steigt die Lebensqualität als Folge der Behandlung)
Daten vorn:
Ergotherapiepraxis

```html
<!DOCTYPE html>
<html lang="de">
<head>
<meta charset="utf-8">
<title>Visitenkarte Ergotherapiepraxis</title>
<link href="https://fonts.googleapis.com/css2?family=Kristi&family=Roboto+Condensed:wght@300&display=swap" rel="stylesheet">
<style>
  :root {
    --page-bg: #f3f2f1;
    --card-top: #f8e3e8;
    --card-bottom: #fdf6f8;
    --blossom-light: #f6c9d3;
    --blossom-deep: #e79aad;
    --ink: #3a3033;
    --ink-soft: #6a5f62;
    --shadow: rgba(0, 0, 0, 0.12);
  }
  * { margin: 0; padding: 0; box-sizing: border-box; }
  html, body {
    width: 1200px; height: 847px; overflow: hidden;
    background: var(--page-bg);
  }
  .sheet { position: relative; width: 1200px; height: 847px; }
  .card {
    position: absolute; top: 238px;
    width: 486px; height: 319px; overflow: hidden;
    background: linear-gradient(180deg, var(--card-top) 0%, var(--card-bottom) 60%);
    box-shadow: 0 2px 6px var(--shadow);
  }
  .card--front { left: 111px; }
  .card--back { left: 616px; }
  .blossoms { position: absolute; left: 0; top: 0; width: 486px; height: 319px; }
  .card__text { position: absolute; left: 0; width: 100%; text-align: center; }
  .name {
    font-family: "Kristi", cursive;
    font-size: 46px; font-weight: 400; color: var(--ink); line-height: 1;
  }
  .role {
    font-family: "Roboto Condensed", sans-serif; font-weight: 300;
    font-size: 17px; letter-spacing: 1.5px; color: var(--ink-soft);
  }
  .address {
    font-family: "Roboto Condensed", sans-serif; font-weight: 300;
    font-size: 17px; line-height: 25px; color: var(--ink-soft); font-style: normal;
  }
  .front-name { top: 44px; }
  .front-role { top: 102px; }
  .front-address { top: 156px; }
  .back-label { top: 108px; left: -26px; }
  .back-name { top: 150px; left: -26px; }
</style>
</head>
<body>
<main class="sheet">
  <section class="card card--front">
    <svg class="blossoms" viewBox="0 0 486 319" role="img" aria-label="Blühende Kirschbäume in Rosatönen am unteren Kartenrand">
      <defs>
        <linearGradient id="bloomFront" x1="0" y1="0" x2="0" y2="1">
          <stop offset="0" stop-color="var(--blossom-light)" stop-opacity="0.35"/>
          <stop offset="0.5" stop-color="var(--blossom-light)" stop-opacity="0.85"/>
          <stop offset="1" stop-color="var(--blossom-deep)"/>
        </linearGradient>
      </defs>
      <path d="M0 140 Q40 125 80 150 Q130 175 170 165 Q230 150 290 175 Q350 160 400 170 Q450 150 486 165 L486 319 L0 319 Z" fill="url(#bloomFront)"/>
    </svg>
    <h1 class="card__text name front-name">Marlene Weiß</h1>
    <p class="card__text role front-role">Ergotherapiepraxis</p>
    <address class="card__text address front-address">
      Am Lindenhof 4<br>
      14950 Wiesental, OT Birkau<br>
      Tel.: 03370 1/48215
    </address>
  </section>

  <section class="card card--back">
    <svg class="blossoms" viewBox="0 0 486 319" role="img" aria-label="Aufsteigende Kirschblüten von links unten nach rechts oben">
      <defs>
        <linearGradient id="bloomBack" x1="0" y1="1" x2="1" y2="0">
          <stop offset="0" stop-color="var(--blossom-deep)"/>
          <stop offset="0.6" stop-color="var(--blossom-light)" stop-opacity="0.9"/>
          <stop offset="1" stop-color="var(--blossom-light)" stop-opacity="0.4"/>
        </linearGradient>
      </defs>
      <path d="M0 200 Q60 185 120 215 Q170 200 220 180 Q260 140 310 125 Q360 90 410 70 Q450 45 486 40 L486 319 L0 319 Z" fill="url(#bloomBack)"/>
    </svg>
    <p class="card__text role back-label">Behandelnder Therapeut:</p>
    <h2 class="card__text name back-name">Marlene Weiß</h2>
  </section>
</main>
</body>
</html>
```